TORV Business Card Neil

Field Capital Advisory (TORV) is a consulting company that advises stakeholders in the Agricultural Industry. Based in rural NSW Australia, we need a good business card. TORV has a lifetime of agricultural experience and knowledge, particularly in the beef, wool and lamb markets. Though it is expanding into other rural ventures. Our clients are primarily off-farm investors who trust our business to advise on the best path forward for their agricultural investment. We also work with large players in the retail sector. Our image is trustworthy, reliable, smart and professional.
Updates

I think the black is too urban, perhaps a dark blue on one side and white on the other, or the yellow/orange on one side and white on the other??

we need to have the tag line "Customised Agribusiness Strategy" and our list of services:

"Due Diligence, Acquisition, Planning, Management, Strategy, Supply Chain" included in the design

we actually have 6 services - the should read in order:

Due diligence
Acquisition
Strategy
Planning 
Management
Supply chain

Target Market(s)

large rural land holders
senior players in agribusiness
senior management of retail food outlets
middle-senior aged men

Industry/Entity Type

Retail

Requirements
Must have
• high quality, 2 sides

logo

"Neil Ashcombe
Director
0413952617
neil@torv.com.au
PO Box 4721, Tallowbrook NSW 2358"

tag line "Customised Agribusiness Strategy"

services provided

"Due diligence
Acquisition
Strategy
Planning
Management
Supply chain"
Should not have
• no images of animals or leaves

```html
<!DOCTYPE html>
<html lang="en">
<head>
<meta charset="UTF-8">
<title>TORV Business Card – Neil Ashcombe</title>
<link href="https://fonts.googleapis.com/css2?family=Oswald:wght@500;600&family=Open+Sans:wght@400;600&family=Cormorant+Garamond:wght@600&display=swap" rel="stylesheet">
<style>
  :root {
    --backdrop: #4a4a4a;
    --card-white: #fbfbfa;
    --brand-blue: #2a5aa8;
    --brand-yellow: #f3b61c;
    --brand-yellow-light: #f7cf2e;
    --brand-orange: #eea51a;
    --text-grey: #6d6d6d;
    --band-text: #ffffff;
  }
  html, body {
    margin: 0;
    width: 1200px;
    height: 1024px;
    overflow: hidden;
    background: radial-gradient(circle at 50% 45%, #6a6a6a 0%, var(--backdrop) 55%, #262626 100%);
    font-family: "Open Sans", sans-serif;
  }
  .card {
    position: absolute;
    left: 240px;
    width: 720px;
    height: 436px;
    box-shadow: 0 14px 30px rgba(0,0,0,.45);
    overflow: hidden;
  }
  .card-front { top: 50px; background: var(--card-white); }
  .brand {
    position: absolute;
    left: 70px;
    top: 62px;
  }
  .brand-name {
    font-family: "Oswald", sans-serif;
    font-weight: 600;
    font-size: 78px;
    line-height: 1;
    letter-spacing: 4px;
    color: var(--brand-blue);
  }
  .brand-sub {
    font-family: "Cormorant Garamond", serif;
    font-weight: 600;
    font-size: 19px;
    letter-spacing: 1.5px;
    text-transform: uppercase;
    color: var(--brand-blue);
    margin-top: 4px;
  }
  .holder {
    position: absolute;
    left: 72px;
    top: 200px;
  }
  .holder-name {
    font-family: "Oswald", sans-serif;
    font-weight: 500;
    font-size: 24px;
    letter-spacing: 1px;
    color: var(--brand-orange);
    text-transform: uppercase;
    line-height: 1.1;
  }
  .holder-role {
    font-size: 14px;
    letter-spacing: 2px;
    color: var(--text-grey);
    text-transform: uppercase;
  }
  .contact-list {
    position: absolute;
    left: 432px;
    top: 198px;
    margin: 0;
    padding: 0;
    list-style: none;
    font-size: 13px;
    color: var(--text-grey);
  }
  .contact-list li {
    display: flex;
    align-items: center;
    gap: 10px;
    height: 24px;
    white-space: nowrap;
  }
  .contact-list svg { width: 12px; height: 12px; fill: var(--brand-yellow); flex: none; }
  .service-band {
    position: absolute;
    left: 0; right: 0; bottom: 0;
    height: 118px;
    background: linear-gradient(90deg, var(--brand-yellow-light), var(--brand-yellow));
    padding: 22px 0 0 72px;
    box-sizing: border-box;
    color: var(--band-text);
  }
  .service-tagline, .service-heading {
    font-family: "Oswald", sans-serif;
    font-weight: 600;
    font-size: 17px;
    letter-spacing: .8px;
    text-transform: uppercase;
    line-height: 1.3;
  }
  .service-list {
    margin: 6px 0 0;
    padding: 0;
    list-style: none;
    display: flex;
    font-size: 13px;
    white-space: nowrap;
  }
  .service-list li + li::before { content: "|"; margin: 0 10px; }

  .card-back {
    top: 538px;
    background: linear-gradient(100deg, var(--brand-yellow) 0%, var(--brand-yellow-light) 55%, var(--brand-yellow) 100%);
  }
  .back-band {
    position: absolute;
    left: 0; right: 0;
    top: 150px;
    height: 136px;
    background: var(--card-white);
  }
  .back-rule {
    position: absolute;
    left: 0; right: 0;
    height: 3px;
    background: var(--card-white);
  }
  .back-rule-top { top: 138px; }
  .back-rule-bottom { top: 295px; }
  .back-band .brand { left: 70px; top: 18px; }
</style>
</head>
<body>
  <section class="card card-front" aria-label="Front of business card">
    <div class="brand">
      <div class="brand-name">TORV</div>
      <div class="brand-sub">Field Capital Advisory</div>
    </div>
    <div class="holder">
      <div class="holder-name">Neil Ashcombe</div>
      <div class="holder-role">Director</div>
    </div>
    <ul class="contact-list">
      <li><svg viewBox="0 0 12 12"><path d="M2 0h3l1 3-2 1a7 7 0 0 0 4 4l1-2 3 1v3a2 2 0 0 1-2 2A10 10 0 0 1 0 2a2 2 0 0 1 2-2z"/></svg>0413 952 617</li>
      <li><svg viewBox="0 0 12 12"><path d="M0 2h12v8H0z M0 2l6 5 6-5"/></svg>neil@torv.com.au</li>
      <li><svg viewBox="0 0 12 12"><path d="M6 0a4 4 0 0 1 4 4c0 3-4 8-4 8S2 7 2 4a4 4 0 0 1 4-4zm0 2.5a1.5 1.5 0 1 0 0 3 1.5 1.5 0 0 0 0-3z"/></svg>PO Box 4721, Tallowbrook NSW 2358</li>
    </ul>
    <div class="service-band">
      <div class="service-tagline">Customised Agribusiness Strategy</div>
      <div class="service-heading">Services Provided</div>
      <ul class="service-list">
        <li>Due diligence</li>
        <li>Acquisition</li>
        <li>Strategy</li>
        <li>Planning</li>
        <li>Management</li>
        <li>Supply chain</li>
      </ul>
    </div>
  </section>

  <section class="card card-back" aria-label="Back of business card">
    <div class="back-rule back-rule-top"></div>
    <div class="back-band">
      <div class="brand">
        <div class="brand-name">TORV</div>
        <div class="brand-sub">Field Capital Advisory</div>
      </div>
    </div>
    <div class="back-rule back-rule-bottom"></div>
  </section>
</body>
</html>
```